Social responsible Renewable Energy company

We at brivoX are an independent power producer company founded in 2021 that handles large scale deployment of Renewable Energy and carbon neutral Energy as a service model. We offer turnkey solutions using solar panel systems and this could be incorporated in our business cards. You can also find our logo in the documents provided. Another key issue is that the business cards will be printed on recicled paper, not sure if this is a limitation in deciding the design. The recycled sign should also be added on the business card and stating that the paper used was recycled. Our website is www.mybrivox-example.com. It should also be very professional, not too dreamy but still needs to capture your imagination. We are really excited to get your ideas !

Target Market(s)

Renewable Energy market

Contact Information for Business Card

The business card will be printed on recycled paper. Name of the company is brivoX. Website is www.mybrivox-example.com

Requirements
Nice to have
• Our motto: Clean energy, shared with every community.

```html
<!DOCTYPE html>
<html lang="en">
<head>
<meta charset="utf-8">
<title>brivoX business card</title>
<link rel="stylesheet" href="https://fonts.googleapis.com/css2?family=Open+Sans:wght@400;600;700&display=swap">
<style>
  :root {
    --backdrop: #e6e6e3;
    --kraft: #c6ab8b;
    --kraft-edge: #b39677;
    --ink: #353535;
    --ink-soft: #4a4744;
  }
  * { box-sizing: border-box; margin: 0; padding: 0; }
  html, body {
    width: 1200px; height: 801px; overflow: hidden;
    background: var(--backdrop);
    font-family: "Open Sans", Arial, sans-serif;
    color: var(--ink);
  }
  .canvas { position: relative; width: 1200px; height: 801px; }
  .card {
    position: absolute;
    width: 525px; height: 300px;
    background: var(--kraft);
    border: 1px solid var(--kraft-edge);
  }
  .card-front { left: 55px; top: 120px; }
  .card-back { left: 620px; top: 380px; }

  .holder { position: absolute; right: 34px; top: 30px; text-align: right; }
  .holder-name { font-weight: 700; font-size: 19px; letter-spacing: 0.5px; }
  .holder-role { font-size: 13px; color: var(--ink-soft); }

  .brand-name {
    position: absolute; left: 34px; top: 96px;
    font-weight: 700; font-size: 56px; letter-spacing: -1px;
    color: var(--ink); line-height: 1;
  }
  .address { position: absolute; left: 38px; top: 172px; font-size: 14px; line-height: 1.35; color: var(--ink-soft); }
  .contacts { position: absolute; left: 38px; top: 222px; list-style: none; font-size: 14px; line-height: 1.45; color: var(--ink-soft); }
  .contacts li { display: flex; align-items: center; gap: 7px; }
  .contacts svg { width: 11px; height: 11px; flex: none; }
  .icon-fill { fill: var(--ink); }
  .icon-line { fill: none; stroke: var(--ink); stroke-width: 2.5; }

  .cert-badge {
    position: absolute; right: 60px; top: 160px;
    width: 54px; height: 60px; border: 3px solid var(--ink); border-radius: 6px;
  }

  .back-mark {
    position: absolute; left: 0; right: 0; top: 95px; text-align: center;
    font-weight: 700; font-size: 52px; letter-spacing: -1px; line-height: 1;
  }
  .motto {
    position: absolute; left: 0; right: 0; bottom: 34px; text-align: center;
    font-size: 16px; color: var(--ink-soft);
  }
</style>
</head>
<body>
<main class="canvas">
  <section class="card card-front">
    <div class="holder">
      <p class="holder-name">DAREN HOLLOWAY</p>
      <p class="holder-role">President</p>
    </div>
    <p class="brand-name">brivoX</p>
    <p class="address">1820 Harbor Crest Way<br>Seaview CA 90410</p>
    <ul class="contacts">
      <li><svg viewBox="0 0 24 24"><path class="icon-fill" d="M6.6 10.8a15.1 15.1 0 0 0 6.6 6.6l2.2-2.2a1 1 0 0 1 1-.25 11.4 11.4 0 0 0 3.6.57 1 1 0 0 1 1 1V20a1 1 0 0 1-1 1A17 17 0 0 1 3 4a1 1 0 0 1 1-1h3.5a1 1 0 0 1 1 1c0 1.25.2 2.45.57 3.6a1 1 0 0 1-.25 1z"/></svg>555-014-2290</li>
      <li><svg viewBox="0 0 24 24"><rect class="icon-line" x="2" y="5" width="20" height="14"/><path class="icon-line" d="M2 5l10 8 10-8"/></svg>dholloway@mybrivox-example.com</li>
      <li><svg viewBox="0 0 24 24"><circle class="icon-fill" cx="12" cy="12" r="10"/></svg>www.mybrivox-example.com</li>
    </ul>
    <div class="cert-badge" role="img" aria-label="Recycled paper certification badge"></div>
  </section>

  <section class="card card-back">
    <p class="back-mark">brivoX</p>
    <p class="motto">Clean energy, shared with every community.</p>
  </section>
</main>
</body>
</html>
```